Catalogue Design Project

We need a catalog design for a new private university called Redwell Institute Bayshore (see website www.rwi-bs.org). The catalog should be about 30 pages maximum and will include items such as General Information, Academic schedule, department descriptions, program descriptions, course descriptions, school policies, student services, admissions, San diego Lifestyle, etc.
I will provide the text but I need a professional design with regard to page layouts. I have provided some examples.
Ok, i posted the catalog content, just missing course descriptions.
Target Market(s)
Young Professionals, Foreign Students
Industry/Entity Type
University
Look and feel
Each slider illustrates characteristics of the customer's brand and the style your logo design should communicate.

```html
<!DOCTYPE html>
<html lang="en">
<head>
<meta charset="utf-8">
<title>Travel/Study Package – Redwell Institute Bayshore</title>
<link rel="stylesheet" href="https://fonts.googleapis.com/css2?family=Carlito:wght@400;700&display=swap">
<style>
  :root {
    --ink: #1a1a1a;
    --navy: #1f4f80;
    --rule: #3d6b9a;
    --muted: #8a8a8a;
    --paper: #ffffff;
    --sand-light: #f6efe2;
    --sand: #d9c59f;
    --sky: #c9d3ea;
    --lilac: #e7d6ee;
    --map: #c8a88e;
  }
  * { margin: 0; padding: 0; box-sizing: border-box; }
  html, body { width: 927px; height: 1200px; overflow: hidden; background: var(--paper); }
  body { font-family: "Carlito", "Calibri", sans-serif; color: var(--ink); }
  .page { position: relative; width: 927px; height: 1200px; overflow: hidden; }

  .brand {
    position: absolute; left: 61px; top: 38px;
    display: flex; align-items: center; gap: 10px;
    font-size: 19px; font-weight: 700; color: var(--navy);
  }
  .brand-dot { width: 16px; height: 16px; border-radius: 50%; background: var(--navy); }

  .header-photo {
    position: absolute; right: 0; top: 0; width: 360px; height: 100px;
    background: linear-gradient(90deg, rgba(255,255,255,1) 0%, var(--sand-light) 35%, var(--sand) 75%, #e9dcc2 100%);
  }
  .header-rule { position: absolute; left: 0; top: 102px; width: 927px; height: 2px; background: var(--rule); }
  .section-tab { position: absolute; right: 0; top: 103px; width: 400px; height: 42px; }
  .section-tab-label {
    position: absolute; right: 20px; top: 106px;
    font-size: 31px; color: #fff; letter-spacing: 0.3px; line-height: 38px;
  }

  .page-title {
    position: absolute; left: 0; top: 188px; width: 927px; text-align: center;
    font-size: 25px; font-weight: 700;
  }
  .hero {
    position: absolute; left: 67px; top: 235px; width: 818px; height: 398px;
    background:
      radial-gradient(ellipse at 25% 40%, var(--map) 0%, rgba(200,168,142,0) 45%),
      linear-gradient(180deg, var(--lilac) 0%, var(--sky) 45%, #f3eef6 100%);
  }

  .body-copy {
    position: absolute; left: 80px; top: 650px; width: 805px;
    font-size: 19.5px; line-height: 41px; text-align: justify;
  }
  .body-copy .contact { margin-top: 41px; }

  .footer-rule { position: absolute; left: 0; top: 1159px; width: 927px; height: 1px; background: var(--rule); }
  .folio {
    position: absolute; right: 36px; top: 1170px;
    font-size: 14px; color: var(--muted); letter-spacing: 0.3px;
  }
</style>
</head>
<body>
<div class="page">
  <div class="brand"><span class="brand-dot"></span>Redwell Institute Bayshore</div>

  <div class="header-photo" role="img" aria-label="Open antique book resting on a desk, fading into white"></div>
  <div class="header-rule"></div>
  <svg class="section-tab" viewBox="0 0 400 42" aria-hidden="true">
    <polygon points="22,0 400,0 400,42 0,42" fill="var(--navy)"/>
  </svg>
  <div class="section-tab-label">TRAVEL/STUDY PACKAGE</div>

  <h1 class="page-title">Travel/Study Package for American Students</h1>

  <div class="hero" role="img" aria-label="Hand pointing at a city map beside fifteen round national flag badges of partner countries floating over clouds"></div>

  <div class="body-copy">
    <p>With partnerships across 15 different countries, RWIB offers local students the opportunity of a lifetime to study, work, and travel to the destination of their choice for a short or long-term stay.</p>
    <p>Ideal for business professionals wanting to advance their careers by acquiring a foreign language while at the same time, enjoying a new life and being exposed to a new culture. Countries include Brazil, Argentina, Chile, Costa Rica, Mexico, China, Taiwan, Japan, South Korea, Vietnam, Thailand, Spain, Portugal, Turkey and Italy. Most packages include round-trip airfare, housing, and class enrollment; some include job placement.</p>
    <p class="contact">Please contact the university for more details.</p>
  </div>

  <div class="footer-rule"></div>
  <div class="folio">17::: REDWELL INSTITUTE</div>
</div>
</body>
</html>
```